Yacht, Boats, Watersports company needs a redesign of business card

Hello Designers!
We are a Boat dealership company that sells fun in the water, we sell boats, Yachts, Kayaks and also yacht WaterSport toys. We are looking to redesign our business cards in to something a little bit more sophisticated. in a way that we can make better use of our company colors. I'm attaching a zipped file containing the company 3 sets of company logo which one is an horizontal another one is a vertical and also a chromed 3d logo. Also is included two set of business cards that we use and also some designs that i think it's interesting. We use PMS 2026c Orange and PMS 7687C Blue. I would like to see at least two different options with the orange as accent and also using blue as an accent color. It's really important for the business cards to have a font option and size that is legible to most people. Our current website is wwww.coralpennant.com. Please visit if you want to have a better feeling of the Boat dealership
You can send Single sided or double side options. We are now using single sided but we may be open for a double side option if we really like the design.
Target Market(s)
Marine, boat sales, yacht sales, water toys sales/
Contact Information for Business Card
Name: Dale Whitcombe
Address: 212 North Fenwick Lane,
Marlin Cove, FL 33051
Phone: 954-731-8842
Fax: 954:731-8843
Cell: 954-382-1490
Email: dw@coralpennant.com
Website: coralpennant.com
Requirements
Must have
- the current information of the business card provided.
logo
use the PMS Colors
Nice to have
- a touch of elegance and sophistication but simple
Should not have
- should not have any typography that is hard to read, the card should be simple but yet sophisticated.

```html
<!DOCTYPE html>
<html lang="en">
<head>
<meta charset="utf-8">
<title>Coral Pennant – Business Card</title>
<link href="https://fonts.googleapis.com/css2?family=Montserrat:wght@400;500;800&display=swap" rel="stylesheet">
<style>
  :root {
    --brand-blue: #1f4689;
    --brand-orange: #e87a24;
    --paper: #ffffff;
    --backdrop: #ffffff;
  }
  html, body {
    margin: 0;
    padding: 0;
    width: 1200px;
    height: 964px;
    overflow: hidden;
    background: var(--backdrop);
    font-family: "Montserrat", sans-serif;
  }
  .card {
    position: absolute;
    left: 24px;
    top: 153px;
    width: 1151px;
    height: 657px;
    border-radius: 42px;
    background: var(--paper);
    overflow: hidden;
  }
  .card-waves {
    position: absolute;
    inset: 0;
    width: 1151px;
    height: 657px;
  }
  .wave-blue { fill: var(--brand-blue); }
  .wave-orange { fill: var(--brand-orange); }

  .brand {
    position: absolute;
    left: 64px;
    top: 88px;
    display: flex;
    align-items: center;
    gap: 14px;
  }
  .brand-dot {
    width: 22px;
    height: 22px;
    border-radius: 50%;
    background: var(--brand-orange);
  }
  .brand-name {
    font-weight: 800;
    font-size: 38px;
    letter-spacing: 1.5px;
    color: var(--brand-blue);
    text-transform: uppercase;
    line-height: 1;
  }

  .person {
    position: absolute;
    left: 66px;
    top: 348px;
  }
  .person-name {
    margin: 0;
    font-weight: 800;
    font-size: 40px;
    letter-spacing: 4px;
    color: var(--brand-orange);
    text-transform: uppercase;
    line-height: 44px;
  }
  .person-role {
    margin: 0;
    font-weight: 400;
    font-size: 22px;
    letter-spacing: 2px;
    color: var(--paper);
    line-height: 28px;
  }

  .contact-list {
    position: absolute;
    left: 62px;
    top: 453px;
    margin: 0;
    padding: 0;
    list-style: none;
  }
  .contact-list li,
  .address {
    display: flex;
    align-items: center;
    gap: 16px;
    height: 34px;
    font-size: 22px;
    font-weight: 400;
    letter-spacing: 2px;
    color: var(--paper);
  }
  .icon {
    width: 22px;
    height: 22px;
    fill: var(--brand-orange);
    flex: none;
  }
  .accent { color: var(--brand-orange); }

  .address {
    position: absolute;
    left: 522px;
    top: 559px;
    height: auto;
    gap: 24px;
  }
  .address p {
    margin: 0;
    line-height: 32px;
  }
</style>
</head>
<body>
  <div class="card">
    <svg class="card-waves" viewBox="0 0 1151 657" aria-hidden="true">
      <path class="wave-orange" d="M0 325 C 150 235 360 215 609 382 C 390 260 170 255 0 340 Z"/>
      <path class="wave-blue" d="M0 355 C 150 265 360 255 600 380 C 760 460 820 483 881 483 C 1000 483 1090 420 1151 322 L1151 657 L0 657 Z"/>
    </svg>

    <div class="brand">
      <span class="brand-dot"></span>
      <span class="brand-name">Coral Pennant</span>
    </div>

    <div class="person">
      <h1 class="person-name">Dale Whitcombe</h1>
      <p class="person-role">Founder &amp; CEO</p>
    </div>

    <ul class="contact-list">
      <li>
        <svg class="icon" viewBox="0 0 24 24"><path d="M2 9c0-3 5-5 10-5s10 2 10 5v2h-5V8.5c-3-1-7-1-10 0V11H2zM6 12l2-3h8l2 3v7H6zm6 1.5a2.5 2.5 0 1 0 0 5 2.5 2.5 0 0 0 0-5z"/></svg>
        <span>954-731-8842</span>
      </li>
      <li>
        <svg class="icon" viewBox="0 0 24 24"><path d="M7 1h10a2 2 0 0 1 2 2v18a2 2 0 0 1-2 2H7a2 2 0 0 1-2-2V3a2 2 0 0 1 2-2zm0 3v14h10V4zm5 15.5a1.2 1.2 0 1 0 0 2.4 1.2 1.2 0 0 0 0-2.4z"/></svg>
        <span>954-382-1490</span>
      </li>
      <li>
        <svg class="icon" viewBox="0 0 24 24"><path d="M6 2h12v5H6zM3 8h18a2 2 0 0 1 2 2v7h-4v-3H5v3H1v-7a2 2 0 0 1 2-2zm4 7h10v7H7z"/></svg>
        <span>954:731-8843</span>
      </li>
      <li>
        <svg class="icon" viewBox="0 0 24 24"><path d="M1 5h22v14H1zm2 2v.5l9 6 9-6V7zm0 3v7l5-3.5zm18 0-5 3.5 5 3.5z"/></svg>
        <span>dw@coralpennant.com</span>
      </li>
      <li>
        <svg class="icon" viewBox="0 0 24 24"><path d="M12 1a11 11 0 1 0 0 22 11 11 0 0 0 0-22zm0 2c1.3 1.6 2.2 3.7 2.5 6h-5C9.8 6.7 10.7 4.6 12 3zm-3 .6C8.2 5.2 7.7 7 7.5 9H3.6A9 9 0 0 1 9 3.6zm6 0A9 9 0 0 1 20.4 9h-3.9c-.2-2-.7-3.8-1.5-5.4zM3.3 11h4.2v2H3.3zm6.2 0h5v2h-5zm7 0h4.2v2h-4.2zM3.6 15h3.9c.2 2 .7 3.8 1.5 5.4A9 9 0 0 1 3.6 15zm5.9 0h5c-.3 2.3-1.2 4.4-2.5 6-1.3-1.6-2.2-3.7-2.5-6zm7 0h3.9a9 9 0 0 1-5.4 5.4c.8-1.6 1.3-3.4 1.5-5.4z"/></svg>
        <span>www.<span class="accent">coralpennant</span>.com</span>
      </li>
    </ul>

    <div class="address">
      <svg class="icon" viewBox="0 0 24 24"><path d="M12 1a8 8 0 0 0-8 8c0 6 8 14 8 14s8-8 8-14a8 8 0 0 0-8-8zm0 5a3 3 0 1 1 0 6 3 3 0 0 1 0-6z"/></svg>
      <div>
        <p>212 North Fenwick Lane,</p>
        <p>Marlin Cove, FL 33051</p>
      </div>
    </div>
  </div>
</body>
</html>
```